PowerPoint Presentation 10 Slides Needed with custom graphics and possibly animated gifs

I'm creating an educational webinar for professionals. I have 10 slides that need special treatment--effective visuals that really Deliverables10 PowerPoint slides in shared PPT fileWith 10 or more images that communicate the message described in the slides notes for each slide.DeadlineSlides will be used in a PowerPoint presentation Monday, Dec 10.Due date is Friday, Dec 7.Design GuidanceSee attached deck for existing design template/theme (with colors/logo)You should match the designAnimations should be delivered as GIF files that can appear in a slideAnimation can last 4 to 10 seconds.Instead of animations, photos from Framebarrel can be recommended (I have an account and can provide the final file to use).

```html
<!DOCTYPE html>
<html lang="en">
<head>
<meta charset="utf-8">
<title>Second 6 Slides Modified</title>
<link href="https://fonts.googleapis.com/css2?family=Fira+Sans:wght@400;600;700&family=Oswald:wght@500&display=swap" rel="stylesheet">
<style>
:root{
  --blue:#22409a;
  --green:#137337;
  --orange:#e8a10c;
  --grey-text:#6d6e71;
  --headline-grey:#7f8184;
  --slide-bg:linear-gradient(200deg,#ffffff 0%,#eeeff1 35%,#e6e7e9 100%);
  --ink:#231f20;
}
*{margin:0;padding:0;box-sizing:border-box}
html,body{width:1200px;height:1056px;overflow:hidden;background:#fff}
.board{position:absolute;left:0;top:0;width:1427px;height:1256px;transform:scale(.8409);transform-origin:0 0;font-family:"Fira Sans",sans-serif;border:1px solid #555}
.board-title{position:absolute;left:1062px;top:50px;font-family:"Oswald",sans-serif;font-size:25px;color:var(--ink);letter-spacing:-.3px}
.slide-number{position:absolute;font-size:22px;color:var(--ink)}
.slide{position:absolute;width:601px;height:337px;background:var(--slide-bg);overflow:hidden}
.slide-title{position:absolute;font-weight:600;font-size:18.5px;color:var(--blue);white-space:nowrap}
.brand{position:absolute;right:40px;top:26px;display:flex;align-items:center;gap:5px;font-weight:600;font-size:11px;color:var(--blue)}
.brand-dot{width:14px;height:14px;border-radius:50%;border:1.5px solid var(--green)}
.side-bar{position:absolute;left:0;top:113px;width:16px;height:141px}
.side-bar.blue{background:var(--blue)}
.side-bar.green{background:var(--green)}
.side-copy{position:absolute;left:34px;font-size:13px;line-height:15.5px;white-space:nowrap}
.side-copy.blue{color:var(--blue)}
.side-copy.green{color:var(--green)}
.rule{position:absolute;left:34px;width:76px;height:2px;background:var(--blue)}
.photo{position:absolute;background:linear-gradient(160deg,#c9b9a8,#6b5a4e)}
.photo.round{border-radius:50%;border:1.5px solid #fff}
.caps{position:absolute;font-family:"Oswald",sans-serif;font-weight:500;white-space:nowrap}
.bubble-text{position:absolute;text-align:center;font-weight:700;font-size:11px;line-height:13px}
.message-headline{left:0;width:601px;top:104px;text-align:center;font-size:36px;line-height:43px;color:var(--headline-grey);letter-spacing:-.2px}
.glove{position:absolute;top:196px;width:46px;height:28px;border:1.5px solid var(--blue)}
.glove.left{left:98px;border-radius:14px 6px 6px 14px}
.glove.right{left:468px;border-radius:6px 14px 14px 6px}
/* facets */
.facet-label{position:absolute;font-weight:600;font-size:11.5px;line-height:13px;color:var(--blue);padding-bottom:5px;white-space:nowrap}
.facet-label::after{content:"";position:absolute;left:0;bottom:0;width:76px;height:2px;background:var(--blue)}
.facet-value{position:absolute;font-size:11.5px;line-height:13px;color:var(--grey-text);white-space:nowrap}
.bias{position:absolute;width:96px;height:96px;border-radius:50%;background:var(--green);box-shadow:0 0 0 3px #fff,0 0 0 4px var(--green);color:#fff;font-family:"Oswald",sans-serif;font-weight:500;font-size:14px;line-height:18px;display:flex;align-items:center;justify-content:center;text-align:center}
.bias-icon{position:absolute;width:40px;height:40px;border-radius:50%;background:#fff;border:2px solid var(--green)}
</style>
</head>
<body>
<div class="board">
  <div class="board-title">SECOND 6 SLIDES MODIFIED</div>

  <div class="slide-number" style="left:42px;top:320px">7</div>
  <div class="slide-number" style="left:42px;top:594px">8</div>
  <div class="slide-number" style="left:42px;top:867px">9</div>
  <div class="slide-number" style="left:1360px;top:340px">10</div>
  <div class="slide-number" style="left:1360px;top:612px">11</div>
  <div class="slide-number" style="left:1360px;top:885px">12</div>

  <!-- Slide 7 -->
  <section class="slide" style="left:86px;top:141px">
    <h2 class="slide-title" style="left:177px;top:31px">What is your role ?</h2>
    <div class="brand"><span>Clientwise</span><span class="brand-dot"></span></div>
    <div class="side-bar blue"></div>
    <p class="side-copy blue" style="top:133px">Two of the common<br>communication roles<br>you adopt to do<br>your job</p>
    <div class="caps" style="left:205px;top:107px;font-size:19px;color:var(--green)">PRIMARY COMMUNICATOR</div>
    <div class="caps" style="left:429px;top:107px;font-size:19px;color:var(--blue)">FACILITATOR</div>
    <svg style="position:absolute;left:225px;top:148px" width="140" height="125" viewBox="0 0 140 125">
      <path d="M70 4C36 4 9 29 9 59c0 22 14 41 35 50l-10 14 28-10c3 1 6 1 8 1 34 0 61-25 61-55S104 4 70 4z" fill="#fff" stroke="var(--green)" stroke-width="1.3"/>
    </svg>
    <svg style="position:absolute;left:355px;top:145px" width="135" height="125" viewBox="0 0 135 125">
      <path d="M63 4C32 4 6 29 6 59s26 55 57 55c6 0 12-1 17-3l26 11-8-18c20-10 33-27 33-45C131 29 97 4 63 4z" fill="#fff" stroke="var(--blue)" stroke-width="1.3"/>
    </svg>
    <div class="photo round" role="img" aria-label="Photo of a smiling professional on a phone call" style="left:162px;top:171px;width:90px;height:90px"></div>
    <div class="photo round" role="img" aria-label="Photo of colleagues exchanging information in an office" style="left:463px;top:153px;width:102px;height:102px;background:linear-gradient(160deg,#8a8a8a,#3a3a3a)"></div>
    <p class="bubble-text" style="left:252px;top:194px;width:105px;color:var(--green)">You have and<br>understand<br>the information</p>
    <p class="bubble-text" style="left:363px;top:194px;width:100px;color:var(--blue)">You help others,<br>SMEs, exchange<br>information</p>
  </section>

  <!-- Slide 8 -->
  <section class="slide" style="left:86px;top:497px">
    <h2 class="slide-title" style="left:176px;top:31px">Communication Styles</h2>
    <div class="brand"><span>Clientwise</span><span class="brand-dot"></span></div>
    <div class="side-bar green" style="top:103px"></div>
    <p class="side-copy blue" style="top:118px">Important to understand<br>your own communication<br>style</p>
    <div class="rule" style="top:177px"></div>
    <p class="side-copy green" style="top:191px">Required to understand<br>your customers<br>communication style</p>
    <p style="position:absolute;left:39px;top:271px;font-size:11px;line-height:12.5px;color:var(--grey-text);text-align:center;width:124px">Adapt your message and<br>style accordingly</p>
    <svg style="position:absolute;left:236px;top:90px" width="140" height="130" viewBox="0 0 140 130">
      <path d="M70 2C33 2 3 25 3 53c0 22 18 40 43 48l-8 26 30-24c1 0 2 0 2 0 37 0 67-23 67-50S107 2 70 2z" fill="var(--green)"/>
    </svg>
    <svg style="position:absolute;left:392px;top:100px" width="155" height="130" viewBox="0 0 155 130">
      <path d="M4 10L150 2l-4 88-54 4-20 30 2-29-68 3z" fill="var(--orange)"/>
    </svg>
    <p class="bubble-text" style="left:240px;top:122px;width:120px;color:#fff">I would like to<br>receive and read<br>information in<br>advance</p>
    <p class="bubble-text" style="left:405px;top:132px;width:125px;color:#fff">I people prefer to<br>receive a verbal<br>summary</p>
    <div class="photo" role="img" aria-label="Photo of a smiling man in a suit holding up a speech bubble" style="left:215px;top:192px;width:130px;height:145px;background:linear-gradient(180deg,#d8c2ad 0%,#3a4457 60%)"></div>
    <div class="photo" role="img" aria-label="Photo of a smiling woman holding up a speech bubble" style="left:382px;top:186px;width:160px;height:151px;background:linear-gradient(180deg,#7a5a45 0%,#1f6b5c 60%,#e8e4dc 100%)"></div>
  </section>

  <!-- Slide 9 -->
  <section class="slide" style="left:86px;top:855px">
    <h2 class="slide-title" style="left:176px;top:31px">Cognitive Biases</h2>
    <div class="brand"><span>Clientwise</span><span class="brand-dot"></span></div>
    <div class="side-bar blue" style="top:103px"></div>
    <p class="side-copy blue" style="top:116px">Important to understand<br>your own cognitive<br>biases and how they can<br>complicate communication</p>
    <div class="rule" style="top:189px"></div>
    <p class="side-copy green" style="top:203px">Required to understand<br>your customer’s  customer’s.</p>
    <div class="bias" style="left:233px;top:148px">CONFIRMATION<br>BIAS</div>
    <div class="bias" style="left:342px;top:148px">HALO<br>AFFECT</div>
    <div class="bias" style="left:456px;top:148px">FALSE<br>CONSENSUS<br>EFFECT</div>
    <div class="bias-icon" role="img" aria-label="Neutral expression icon" style="left:260px;top:108px"></div>
    <div class="bias-icon" role="img" aria-label="Halo expression icon" style="left:370px;top:108px"></div>
    <div class="bias-icon" role="img" aria-label="Group of people icon" style="left:484px;top:108px"></div>
    <p style="position:absolute;left:131px;top:274px;width:420px;font-size:8.5px;line-height:10.5px;color:var(--grey-text)">Via Best Practices, we’ll look at ways to minimize these but it’s important to remembers we like to assume others think like we do, agree with us (way more than they actually do).</p>
  </section>

  <!-- Slide 10 -->
  <section class="slide" style="left:732px;top:142px">
    <h2 class="slide-title" style="left:165px;top:32px">How is your Message</h2>
    <div class="brand"><span>Clientwise</span><span class="brand-dot"></span></div>
    <div class="caps message-headline">THE MESSAGE IS ARGUABLY<br>ONE OF THE MOST<br>CHALLENGING PARTS<br>OF COMMUNICATION.</div>
    <div class="glove left" role="img" aria-label="Outline boxing glove facing right"></div>
    <div class="glove right" role="img" aria-label="Outline boxing glove facing left"></div>
    <div style="position:absolute;left:234px;top:321px;width:141px;height:16px;background:var(--green)"></div>
  </section>

  <!-- Slide 11 -->
  <section class="slide" style="left:732px;top:505px">
    <h2 class="slide-title" style="left:157px;top:32px">Facets of your Message</h2>
    <div class="brand"><span>Clientwise</span><span class="brand-dot"></span></div>
    <div class="side-bar green" style="top:103px"></div>
    <div role="img" aria-label="Line drawing of a faceted diamond" style="position:absolute;left:28px;top:135px;width:104px;height:80px;background:linear-gradient(135deg,rgba(34,64,154,.18),rgba(34,64,154,.05))"></div>
    <div class="facet-label" style="left:156px;top:105px">Information type:</div>
    <div class="facet-label" style="left:310px;top:105px">Complexity:</div>
    <div class="facet-label" style="left:451px;top:105px">Quality:</div>
    <p class="facet-value" style="left:156px;top:136px">Objective (fact/reference),<br>subjective (opinion,<br>recommended<br>guidance)</p>
    <p class="facet-value" style="left:310px;top:136px">Simple or<br>detailed</p>
    <p class="facet-value" style="left:451px;top:136px">How correct<br>and effective is it?</p>
    <div class="facet-label" style="left:156px;top:206px">Requirements<br>to understand:</div>
    <div class="facet-label" style="left:310px;top:206px">Packaging/how it’s<br>communicated:</div>
    <div class="facet-label" style="left:451px;top:206px">Medium<br>used:</div>
    <p class="facet-value" style="left:156px;top:250px">Layman, SME?</p>
    <p class="facet-value" style="left:310px;top:250px">Text, Audio, Visual,<br>Physical/virtual<br>models</p>
    <p class="facet-value" style="left:451px;top:250px">In-person speaking,<br>text, email</p>
  </section>

  <!-- Slide 12 -->
  <section class="slide" style="left:732px;top:863px">
    <h2 class="slide-title" style="left:165px;top:31px">How clear is your message ?</h2>
    <div class="brand"><span>Clientwise</span><span class="brand-dot"></span></div>
    <div class="side-bar blue" style="top:103px"></div>
    <p class="side-copy blue" style="left:44px;top:123px;line-height:17px">No matter how clear<br>we think we’re<br>communicating,<br>others can misinterpret<br>our message.</p>
    <svg style="position:absolute;left:200px;top:100px" width="360" height="190" viewBox="0 0 360 190">
      <ellipse cx="100" cy="72" rx="75" ry="63" fill="var(--blue)"/>
      <circle cx="38" cy="153" r="5.5" fill="var(--blue)"/>
      <circle cx="24" cy="163" r="4" fill="var(--blue)"/>
      <circle cx="9" cy="175" r="2.5" fill="var(--blue)"/>
      <ellipse cx="264" cy="72" rx="75" ry="63" fill="var(--green)"/>
      <circle cx="326" cy="150" r="5.5" fill="var(--green)"/>
      <circle cx="340" cy="160" r="4" fill="var(--green)"/>
    </svg>
    <div role="img" aria-label="Clean spiral graphic" style="position:absolute;left:258px;top:130px;width:84px;height:84px;border-radius:50%;border:2px solid rgba(255,255,255,.7)"></div>
    <div role="img" aria-label="Tangled scribble graphic" style="position:absolute;left:422px;top:130px;width:84px;height:84px;border-radius:50%;background:rgba(255,255,255,.18)"></div>
  </section>
</div>
</body>
</html>
```